Redesign for existing homepage

We would like a redesign for our websites 2 column homepage
We provide engine repair and reconditioning services
We would like a cleaner, modern site that works well with our logo colors
Please see the attached brief for more info
Target Market(s)
25 - 45
Industry/Entity Type
Cleaner
Requirements
Must have
- Google Fonts

```html
<!DOCTYPE html>
<html lang="en">
<head>
<meta charset="utf-8">
<title>Harbourline Engines</title>
<link href="https://fonts.googleapis.com/css2?family=Roboto:wght@400;500;700&family=Open+Sans:wght@400;600;700&display=swap" rel="stylesheet">
<style>
:root{
  --black:#000;
  --yellow:#ffd84a;
  --yellow-deep:#f7c21a;
  --orange:#f7931e;
  --gold:#f2d21b;
  --panel:#1b1b1b;
  --footer:#4a4a4a;
  --white:#fff;
  --grey-text:#cfcfcf;
  --link:#1a5fd0;
}
*{margin:0;padding:0;box-sizing:border-box}
html,body{width:864px;height:1200px;overflow:hidden;background:var(--black);font-family:'Roboto',sans-serif;color:var(--white)}
.page{position:relative;width:864px;height:1200px}
.header{position:absolute;top:0;left:0;width:864px;height:106px}
.brand{position:absolute;left:124px;top:36px;display:flex;align-items:center;gap:10px}
.brand-dot{width:28px;height:28px;border-radius:50%;background:var(--yellow-deep)}
.brand-name{font-size:24px;font-weight:700;color:var(--yellow-deep)}
.contact{position:absolute;right:125px;top:34px;text-align:right}
.phone{font-size:20px;display:flex;align-items:center;justify-content:flex-end;gap:8px}
.tagline{font-size:11.5px;margin-top:12px}
.nav{position:absolute;top:106px;left:0;width:864px;height:46px;background:linear-gradient(var(--yellow),#fdc72c);display:flex;padding-left:123px}
.nav a{font-size:10px;color:#222;text-decoration:none;padding:0 10px;line-height:46px;border-right:1px solid rgba(0,0,0,.15)}
.nav a:last-child{border:none}
.nav a.active{background:var(--orange)}
.hero{position:absolute;top:152px;left:0;width:864px;height:399px;background:radial-gradient(ellipse at 50% 45%,#d9b43a 0%,#a9a98a 35%,#c9d2de 70%,#dde3ea 100%)}
.hero h1{position:absolute;left:124px;top:160px;font-size:29px;font-weight:400;line-height:39px;letter-spacing:1px;text-shadow:0 2px 4px rgba(0,0,0,.6)}
.arrow{position:absolute;top:178px;width:37px;height:37px;border-radius:50%;background:#fff;display:flex;align-items:center;justify-content:center}
.card{position:absolute;top:584px;height:108px;background:#fff;color:#222;border:2px solid #fff;display:flex}
.card .img{width:113px;height:100%}
.card .body{flex:1;padding:6px 10px;font-size:7.4px;line-height:11.2px;color:#444}
.card h3{font-size:10px;font-weight:400;color:#111;margin:1px 0 7px}
.card .more{display:block;text-align:right;color:var(--link);margin-top:6px}
.features{position:absolute;left:125px;top:716px;width:300px}
.features h2{font-size:13px;font-weight:400;color:var(--gold);line-height:20px;margin-bottom:11px}
.features p{font-size:10px;line-height:16px;margin-bottom:18px}
.service{position:absolute;left:434px;top:707px;width:307px;height:265px;background:var(--panel);border:1px solid #3a3a3a;padding:0 11px}
.service h2{font-family:'Open Sans',sans-serif;font-size:14px;font-weight:700;color:var(--gold);letter-spacing:1px;padding:15px 0 0 1px;height:46px;border-bottom:1px solid #888}
.service li{list-style:none;display:flex;gap:14px;padding:11px 0 0 8px;height:62px;border-bottom:1px solid #888;font-size:13px;line-height:18px;letter-spacing:.5px}
.service li:last-child{border:none}
.btn{display:inline-block;background:var(--yellow-deep);color:#222;font-family:'Open Sans',sans-serif;font-size:7.5px;font-weight:700;padding:7px 11px;border-radius:2px}
.service .btn{position:absolute;right:18px;bottom:17px}
.footer{position:absolute;top:996px;left:0;width:864px;height:160px;background:var(--footer);font-family:'Open Sans',sans-serif}
.footer h4{font-size:12px;font-weight:400;color:var(--gold);padding-bottom:5px;border-bottom:1px solid #666}
.testi{position:absolute;left:121px;top:12px;width:266px}
.testi h4{padding-left:8px}
.quote{display:flex;gap:8px;margin:8px 0 0 8px}
.avatar{width:54px;height:46px;flex:none;background:linear-gradient(#8a9099,#56606a);border:1px solid #999}
.quote b{font-size:10px;font-weight:600;display:block;margin-bottom:8px}
.quote p{font-size:7.8px;line-height:11px;color:var(--grey-text)}
.testi .btn{margin:10px 0 0 71px}
.divider{position:absolute;left:436px;top:8px;width:1px;height:150px;background:#5d5d5d}
.addr{position:absolute;left:445px;top:12px;width:145px}
.addr p{font-size:8px;margin-top:10px;color:#eee}
.connect{position:absolute;left:446px;top:90px;width:142px}
.socials{position:absolute;left:446px;top:118px;display:flex;gap:32px;font-size:10px;align-items:center}
.socials span{display:flex;align-items:center;gap:8px}
.socials i{width:22px;height:22px;background:#3b3b3b;border-radius:2px}
.copy{position:absolute;top:1171px;width:864px;text-align:center;font-size:7.5px}
</style>
</head>
<body>
<div class="page">
  <header class="header">
    <div class="brand"><span class="brand-dot"></span><span class="brand-name">Harbourline Engines</span></div>
    <div class="contact">
      <div class="phone"><svg width="12" height="20" viewBox="0 0 12 20"><rect x="1" y="1" width="10" height="18" rx="2" fill="none" stroke="#f7c21a" stroke-width="2"/><circle cx="6" cy="15.5" r="1.2" fill="#f7c21a"/></svg>04 555 0142</div>
      <div class="tagline">Engine repairs and reconditioning specialists</div>
    </div>
  </header>
  <nav class="nav">
    <a class="active">HOME</a><a>ABOUT US</a><a>PRIVATE VEHICLE SERVICE &amp; REPAIR</a><a>RACE &amp; CLASSIC CAR ENGINES</a><a>MAKE AN ENQUIRY</a><a>CONTACT US</a>
  </nav>
  <section class="hero" role="img" aria-label="Transparent yellow sports car showing its engine and chassis">
    <h1>Qualified, experienced and friendly<br>engine reconditioning team</h1>
    <div class="arrow" style="left:37px"><svg width="12" height="14"><path d="M9 1 3 7l6 6" fill="none" stroke="#777" stroke-width="3"/></svg></div>
    <div class="arrow" style="left:788px"><svg width="12" height="14"><path d="M3 1l6 6-6 6" fill="none" stroke="#777" stroke-width="3"/></svg></div>
  </section>
  <article class="card" style="left:123px;width:303px">
    <div class="img" role="img" aria-label="Mechanic working on an engine with a wrench" style="background:linear-gradient(135deg,#6d7d8a,#2f3a44 60%,#c95a3a)"></div>
    <div class="body"><h3>WELCOME TO HARBOURLINE</h3>Lorem Ipsum is simply dummy text of the printing and typesetting industry. Lorem Ipsum has been the industry's standard dummy text ever since the 1500s, when an unknown printer took a galley of book. It has survived not only five centuries<span class="more">Read More &gt;&gt;</span></div>
  </article>
  <article class="card" style="left:433px;width:303px">
    <div class="body"><h3 style="font-size:9px;line-height:11px">Specialist engine repair &amp; reconditioning To have your car running at its best</h3>Do you have a personal or family car that needs a repair?<br><span style="display:block;margin-top:4px">Have a classic car that needs specialist engine work?</span><span class="more" style="margin-top:2px">Make an Enquiry &gt;&gt;</span></div>
    <div class="img" role="img" aria-label="Close-up of an engine cylinder head" style="background:linear-gradient(135deg,#bfc3c6,#6c7176 60%,#2d3034)"></div>
  </article>
  <section class="features">
    <h2>PROFESSIONAL AND KNOWLEDGEABLE WORKSHOP STAFF</h2>
    <p>We have an experienced and friendly team that are capable of providing you with a fantastic service.</p>
    <h2 style="width:330px">QUALIFIED &amp; EXPERIENCED ENGINE MACHINISTS</h2>
    <p style="width:300px">The machinists in my workshop are qualified and experienced in their field of work. With all the advancements in modern engine technology, it takes a specialist team to stay up to date.</p>
    <h2>ATTENTION TO THE FINER DETAILS</h2>
    <p>We have an experienced and friendly team that are capable of providing you with a fantastic service.</p>
  </section>
  <section class="service">
    <h2>OUR SERVICE</h2>
    <ul>
      <li><svg width="20" height="20" style="flex:none"><circle cx="10" cy="10" r="10" fill="#f2d21b"/><rect x="8.5" y="4" width="3" height="8" fill="#222"/><rect x="8.5" y="13.5" width="3" height="3" fill="#222"/></svg>Need service and repair for a private vehicle?</li>
      <li><svg width="20" height="20" style="flex:none"><circle cx="10" cy="10" r="10" fill="#f2d21b"/><rect x="8.5" y="4" width="3" height="8" fill="#222"/><rect x="8.5" y="13.5" width="3" height="3" fill="#222"/></svg>Interested in becoming a trade customer?</li>
      <li><svg width="20" height="20" style="flex:none"><circle cx="10" cy="10" r="10" fill="#f2d21b"/><rect x="8.5" y="4" width="3" height="8" fill="#222"/><rect x="8.5" y="13.5" width="3" height="3" fill="#222"/></svg>Is your classic or race car your passion?</li>
    </ul>
    <span class="btn">Read More ›</span>
  </section>
  <footer class="footer">
    <div class="testi">
      <h4>Testimonials</h4>
      <div class="quote">
        <div class="avatar" role="img" aria-label="Customer photo"></div>
        <div><b>Lorem Ipsum</b><p>Lorem Ipsum is simply dummy text of the printing and typesetting industry. Lorem Ipsum has been the industry's standard dummy text ever since the 1500s, when an unknown printer took a galley of type and scrambled it to make a type specimen</p></div>
      </div>
      <span class="btn">Read More</span>
    </div>
    <div class="divider"></div>
    <div class="addr">
      <h4>Address</h4>
      <p>72 Foundry Road, Seaview, Wellington.</p>
      <p>Phone: (04) 555 0187 &nbsp;&nbsp;&nbsp;&nbsp; Fax: (04) 555 0188</p>
    </div>
    <div class="connect"><h4>Connect with US</h4></div>
    <div class="socials"><span><i></i>Community</span><span><i></i>Updates</span><span><i></i>Newsletter</span></div>
  </footer>
  <div class="copy">Copyright © 2014 - All Rights</div>
</div>
</body>
</html>
```